Beauty Salon Mentor Illustration

Hi There, I'm Belinda and I'm a Beauty Salon owner mentor. We are needing 5 different illustration design for a beauty salon coaching business. The pictures will be used on our website next to a small description about our course out line.
Course and what the illustrations will be referring to below:
1. Launch Pad Parlour -Make your dream of owning a salon a reality.
Three options of start-up training and support, teaching must-know insights for beauty therapists who are ready to take the leap to salon owner and want to do it right. Whether you’ve been in the beauty industry a short time or forever, Launch Pad Parlour will set you up for salon success.

2. Chairs Filled Fast - Attract more clients with simple, strategic digital marketing. Chairs Filled Fast educates on the ins and outs of sponsored social media ads. With easy-to-follow video training, you’ll establish your online presence and increase salon bookings.
Learn how to show up on social media with effective strategies that work. Choose our Handled Entirely system, or learn to do it all with our DIY system.

3. Momentum Studio Plan - Transform your salon and your life. Our most tailored program, Momentum Studio Plan offers coaching memberships with Bloom Beauty Hub’s Founder- Belinda. With our results focused framework, you will upskill employees, improve the working environment of the salon and receive leading beauty industry training as we dive into the culture and mindset of your salon. With Belinda as your business mentor and biggest cheerleader get ready to achieve your business goals and move forward with rapid growth.

4. Revive Parlour Path - Successfully put your salon back on the map.
Step into today’s beauty landscape with optimised marketing and industry expertise. If your salon’s been open for a year or even twenty years, Revive Parlour Path will elevate your business, renew your love for your salon and set you up to generate more income. Stand out from the competition as you increase online presence, learn key business development processes and see real results.

5. Skillset Studio Plan - Successfully Upskill and Level Up Your Salon. Skillset Studio Plan offers three training options- In Salon, Online & Diploma of Beauty Therapy. Whether you have your own salon or want to become qualified, Bloom Beauty Hub’s- Skillset Studio Plan adds industry authority and brings specialist expertise to all level of beauty therapists.
Our coaching is based in Australia, aim at female beauty salon owners who are ready to take their business to the next level.

In the files below is just a picture of me so you know who i am. We are wanting the illusion to appeal to a wide audience.

I am the business and everyone i attract into our coaching program works closely with me.

Target Market(s)

Beauty Salon owners; women

Font styles to use
Sans Serif

Colors
fce8d3
fee3d4
fff5ef
fff3d1
f9bb94
fcca95

Requirements
Must have
• Must be relatable to the brief, designs must look great together on the website or separately on their own.
Nice to have
• Industry relatable, engaging to the eye.
Should not have
• i would prefer if there wasn't any words on the illusion

```html
<!DOCTYPE html>
<html lang="en">
<head>
<meta charset="utf-8">
<title>Beauty Salon Mentor Illustration</title>
<link href="https://fonts.googleapis.com/css2?family=Archivo+Black&family=Open+Sans:wght@300;400;600&display=swap" rel="stylesheet">
<style>
  :root {
    --ink: #2b2b2b;
    --grey: #5a5a5a;
    --white: #ffffff;
    --blue: #3a6fd1;
    --blue-light: #74bde8;
    --blue-pale: #cfeefb;
    --navy: #3d5672;
    --cream: #fff3d1;
    --cream-deep: #fcca95;
    --blush: #fee3d4;
    --shell: #fff5ef;
    --rose: #e8627f;
    --peach: #f9bb94;
    --orange: #ef8a4a;
    --sand: #fce8d3;
    --olive: #bfb49a;
  }
  * { box-sizing: border-box; margin: 0; padding: 0; }
  html, body { width: 1200px; height: 1058px; overflow: hidden; }
  body { background: var(--white); font-family: "Open Sans", sans-serif; color: var(--ink); position: relative; }

  .brand-mark { position: absolute; left: 30px; top: 112px; font: 600 34px "Open Sans", sans-serif; color: var(--grey); letter-spacing: 1px; white-space: nowrap; }
  .project-title { position: absolute; left: 30px; top: 226px; width: 370px; font: 400 36px/60px "Archivo Black", sans-serif; letter-spacing: 2.5px; color: var(--ink); text-transform: uppercase; white-space: nowrap; }

  .card { position: absolute; overflow: hidden; box-shadow: 0 10px 22px rgba(0,0,0,0.12); }
  .card-inner { position: absolute; inset: 0; }
  .logo { position: absolute; font: 600 11px "Open Sans", sans-serif; color: var(--grey); white-space: nowrap; }
  .handle { position: absolute; font: 400 11px "Open Sans", sans-serif; white-space: nowrap; }
  .headline { position: absolute; font: 400 25px/30px "Archivo Black", sans-serif; color: var(--ink); white-space: nowrap; }
  .tagline { position: absolute; font: 300 27px/29px "Open Sans", sans-serif; white-space: nowrap; }
  .body-copy { position: absolute; font: 400 10px/13.6px "Open Sans", sans-serif; text-align: justify; }
  .contact-row { position: absolute; display: flex; justify-content: space-between; font: 400 7.2px "Open Sans", sans-serif; white-space: nowrap; }
  .contact-row span { display: flex; align-items: center; gap: 3px; }
  .contact-row svg { width: 7px; height: 7px; }
  .art { position: absolute; }

  /* Momentum Studio Plan */
  .card-momentum { left: 426px; top: 30px; width: 348px; height: 464px; background: var(--white); }
  .card-momentum .logo { left: 15px; top: 22px; }
  .card-momentum .handle { right: 66px; top: 31px; color: var(--blue); }
  .card-momentum .headline { left: 17px; top: 92px; font-size: 22px; line-height: 30px; }
  .card-momentum .tagline { left: 17px; top: 180px; color: var(--blue); }
  .card-momentum .body-copy { left: 15px; top: 298px; width: 318px; color: var(--ink); }
  .card-momentum .contact-row { left: 18px; top: 438px; width: 313px; color: var(--blue); }

  /* Skillset Studio Plan */
  .card-skillset { left: 820px; top: 30px; width: 348px; height: 464px; background: var(--cream); }
  .card-skillset .card-inner { inset: 15px; background: var(--navy); border-radius: 9px; }
  .card-skillset .logo { left: 9px; top: 13px; background: var(--cream); color: var(--navy); padding: 4px 5px; font-size: 8px; }
  .card-skillset .handle { right: 15px; top: 26px; color: var(--cream); }
  .card-skillset .headline { left: 9px; top: 42px; color: var(--white); font-size: 26px; }
  .card-skillset .tagline { left: 9px; top: 73px; color: var(--cream); }
  .card-skillset .body-copy { left: 9px; top: 278px; width: 302px; color: var(--cream); font-size: 10.8px; line-height: 13.6px; text-align: left; letter-spacing: 0.3px; }
  .card-skillset .contact-row { left: 9px; top: 420px; width: 302px; color: var(--cream); }

  /* pink framed cards */
  .card-framed .card-inner { inset: 14px; border: 1px solid var(--rose); border-radius: 6px; }
  .card-framed .logo { left: 10px; top: 15px; font-size: 8px; }
  .card-framed .handle { right: 15px; top: 24px; color: var(--rose); }
  .card-framed .headline { left: 11px; top: 40px; font-size: 23px; }
  .card-framed .tagline { left: 11px; top: 70px; color: var(--rose); font-size: 26px; }
  .card-framed .body-copy { left: 10px; width: 292px; font-size: 11.3px; line-height: 13.6px; letter-spacing: 0.3px; }
  .card-framed .contact-row { left: 10px; top: 416px; width: 292px; color: var(--rose); }

  .card-launch { left: 30px; top: 556px; width: 345px; height: 460px; background: var(--blush); }
  .card-launch .headline { text-transform: uppercase; font-size: 18.5px; letter-spacing: 0.3px; top: 44px; }
  .card-launch .body-copy { top: 306px; }

  .card-revive { left: 426px; top: 556px; width: 346px; height: 460px; background: var(--shell); }
  .card-revive .body-copy { top: 305px; height: 110px; overflow: hidden; }

  /* Chairs Filled Fast */
  .card-chairs { left: 822px; top: 556px; width: 345px; height: 460px; background: var(--white); }
  .card-chairs .logo { left: 15px; top: 23px; }
  .card-chairs .handle { left: 15px; top: 75px; color: var(--orange); }
  .card-chairs .headline { left: 15px; top: 128px; }
  .card-chairs .tagline { left: 15px; top: 197px; color: var(--orange); font-size: 21px; line-height: 22px; }
  .card-chairs .body-copy { left: 15px; top: 295px; width: 317px; font-size: 11.3px; line-height: 13.6px; }
  .card-chairs .body-copy p + p { margin-top: 5px; }
  .card-chairs .contact-row { left: 15px; top: 432px; width: 317px; color: var(--orange); }
</style>
</head>
<body>

  <div class="brand-mark">Bloom Beauty Hub</div>
  <h1 class="project-title">Beauty Salon<br>Mentor<br>Illustration</h1>

  <!-- Momentum Studio Plan -->
  <section class="card card-momentum">
    <svg class="art" width="348" height="464" viewBox="0 0 348 464">
      <path d="M300 0 H348 V270 C330 270 300 258 288 246 C250 220 250 190 280 150 C305 115 290 60 300 0 Z" fill="var(--blue-pale)"/>
      <path d="M320 0 H348 V250 C325 255 296 240 290 225 C280 195 300 170 310 140 C325 90 310 40 320 0 Z" fill="var(--blue-light)"/>
      <circle cx="242" cy="148" r="84" fill="var(--blue)"/>
      <circle cx="246" cy="146" r="80" fill="var(--white)"/>
    </svg>
    <div class="art" role="img" aria-label="Illustration of a relaxed client during a facial, surrounded by spa products" style="left:170px;top:74px;width:146px;height:146px;border-radius:50%;background:radial-gradient(circle,#f3dcc8 0%,#d9eef8 55%,#ffffff 100%);"></div>
    <div class="logo">Bloom Beauty Hub</div>
    <div class="handle">@bloombeautyhub</div>
    <h2 class="headline">Momentum<br>Studio<br>Plan</h2>
    <p class="tagline">Transform<br>your salon<br>and your life.</p>
    <p class="body-copy">Our most tailored program, Momentum Studio Plan offers coaching memberships with Bloom Beauty Hub’s Founder- Belinda. With our results focused framework, you will upskill employees, improve the working environment of the salon and receive leading beauty industry training as we dive into the culture and mindset of your salon. With Belinda as your business mentor and biggest cheerleader get ready to achieve your business goals and move forward with rapid growth.</p>
    <div class="contact-row">
      <span><svg viewBox="0 0 10 10"><path d="M2 1 L4 3 L3 4 C4 6 5 7 6 7 L7 6 L9 8 L7.5 9.5 C4 9 1 6 0.5 2.5 Z" fill="currentColor"/></svg>(+614) 0382 5519</span>
      <span><svg viewBox="0 0 10 10"><rect x="0.5" y="2" width="9" height="6" fill="none" stroke="currentColor"/><path d="M0.5 2 L5 5.5 L9.5 2" fill="none" stroke="currentColor"/></svg>hello@bloombeautyhub.com</span>
      <span><svg viewBox="0 0 10 10"><circle cx="5" cy="5" r="4.3" fill="none" stroke="currentColor"/><path d="M0.7 5 H9.3 M5 0.7 V9.3" stroke="currentColor"/></svg>www.bloombeautyhub.com</span>
    </div>
  </section>

  <!-- Skillset Studio Plan -->
  <section class="card card-skillset">
    <div class="card-inner">
      <div class="art" role="img" aria-label="Illustration of a woman seated on the tallest of three rising pillars beside a ladder and potted plant" style="left:82px;top:134px;width:150px;height:130px;border-radius:8px;background:linear-gradient(180deg,rgba(252,202,149,0.15) 0%,rgba(252,232,211,0.55) 100%);"></div>
      <div class="logo">Bloom Beauty Hub</div>
      <div class="handle">@bloombeautyhub</div>
      <h2 class="headline">Skillset Studio Plan</h2>
      <p class="tagline">Successfully Upskill and<br>Level Up Your Salon.</p>
      <p class="body-copy">Skillset Studio Plan offers three training options- In Salon, Online &amp; Diploma of Beauty Therapy. Whether you have your own salon or want to become qualified, Bloom Beauty Hub’s- Skillset Studio Plan adds industry authority and brings specialist expertise to all level of beauty therapists.<br>Our coaching is based in Australia, aim at female beauty salon owners who are ready to take their business to the next level.</p>
      <div class="contact-row">
        <span><svg viewBox="0 0 10 10"><path d="M2 1 L4 3 L3 4 C4 6 5 7 6 7 L7 6 L9 8 L7.5 9.5 C4 9 1 6 0.5 2.5 Z" fill="currentColor"/></svg>(+614) 0382 5519</span>
        <span><svg viewBox="0 0 10 10"><rect x="0.5" y="2" width="9" height="6" fill="none" stroke="currentColor"/><path d="M0.5 2 L5 5.5 L9.5 2" fill="none" stroke="currentColor"/></svg>hello@bloombeautyhub.com</span>
        <span><svg viewBox="0 0 10 10"><circle cx="5" cy="5" r="4.3" fill="none" stroke="currentColor"/><path d="M0.7 5 H9.3 M5 0.7 V9.3" stroke="currentColor"/></svg>www.bloombeautyhub.com</span>
      </div>
    </div>
  </section>

  <!-- Launch Pad Parlour -->
  <section class="card card-framed card-launch">
    <div class="card-inner">
      <div class="art" role="img" aria-label="Illustration of a woman in a hair towel splashing water on her face, framed by leaves" style="left:70px;top:140px;width:174px;height:152px;border-radius:50% 50% 10px 10px;background:radial-gradient(circle at 50% 45%,#f3d9c2 0%,#ddd3bd 55%,var(--olive) 100%);"></div>
      <div class="logo">Bloom Beauty Hub</div>
      <div class="handle">@bloombeautyhub</div>
      <h2 class="headline">Launch Pad Parlour</h2>
      <p class="tagline">Make your dream of<br>owning a salon a reality.</p>
      <p class="body-copy">Three options of start-up training and support, teaching must-know insights for beauty therapists who are ready to take the leap to salon owner and want to do it right. Whether you’ve been in the beauty industry a short time or forever, Launch Pad Parlour will set you up for salon success.</p>
      <div class="contact-row">
        <span><svg viewBox="0 0 10 10"><path d="M2 1 L4 3 L3 4 C4 6 5 7 6 7 L7 6 L9 8 L7.5 9.5 C4 9 1 6 0.5 2.5 Z" fill="currentColor"/></svg>(+614) 0382 5519</span>
        <span><svg viewBox="0 0 10 10"><rect x="0.5" y="2" width="9" height="6" fill="none" stroke="currentColor"/><path d="M0.5 2 L5 5.5 L9.5 2" fill="none" stroke="currentColor"/></svg>hello@bloombeautyhub.com</span>
        <span><svg viewBox="0 0 10 10"><circle cx="5" cy="5" r="4.3" fill="none" stroke="currentColor"/><path d="M0.7 5 H9.3 M5 0.7 V9.3" stroke="currentColor"/></svg>www.bloombeautyhub.com</span>
      </div>
    </div>
  </section>

  <!-- Revive Parlour Path -->
  <section class="card card-framed card-revive">
    <div class="card-inner">
      <div class="art" role="img" aria-label="Illustration of a woman holding a large number one beside a hashtag symbol and potted plant" style="left:96px;top:138px;width:128px;height:140px;border-radius:50% 50% 8px 8px;background:radial-gradient(circle at 50% 40%,#e9d2c4 0%,#e8c9c2 55%,var(--cream) 100%);"></div>
      <div class="logo">Bloom Beauty Hub</div>
      <div class="handle">@bloombeautyhub</div>
      <h2 class="headline">Revive Parlour Path</h2>
      <p class="tagline">Successfully put your<br>salon back on the map.</p>
      <p class="body-copy">Step into today’s beauty landscape with optimised marketing and industry expertise. If your salon’s been open for a year or even twenty years, Revive Parlour Path will elevate your business, renew your love for your salon and set you up to generate more income. Stand out from the competition as you increase online presence, learn key business development processes and see real results.</p>
      <div class="contact-row">
        <span><svg viewBox="0 0 10 10"><path d="M2 1 L4 3 L3 4 C4 6 5 7 6 7 L7 6 L9 8 L7.5 9.5 C4 9 1 6 0.5 2.5 Z" fill="currentColor"/></svg>(+614) 0382 5519</span>
        <span><svg viewBox="0 0 10 10"><rect x="0.5" y="2" width="9" height="6" fill="none" stroke="currentColor"/><path d="M0.5 2 L5 5.5 L9.5 2" fill="none" stroke="currentColor"/></svg>hello@bloombeautyhub.com</span>
        <span><svg viewBox="0 0 10 10"><circle cx="5" cy="5" r="4.3" fill="none" stroke="currentColor"/><path d="M0.7 5 H9.3 M5 0.7 V9.3" stroke="currentColor"/></svg>www.bloombeautyhub.com</span>
      </div>
    </div>
  </section>

  <!-- Chairs Filled Fast -->
  <section class="card card-chairs">
    <svg class="art" width="345" height="460" viewBox="0 0 345 460">
      <path d="M125 0 H345 V240 C300 250 240 240 200 225 C165 212 150 190 160 185 C185 205 230 218 270 212 C320 205 345 170 345 120 V0 Z" fill="var(--peach)"/>
      <path d="M125 0 C115 40 120 80 145 115 C170 150 200 170 240 180 L345 180 V0 Z" fill="var(--peach)"/>
      <circle cx="245" cy="98" r="83" fill="var(--white)"/>
    </svg>
    <div class="art" role="img" aria-label="Illustration of a woman relaxing with a phone and coffee beside a plant and an online booking screen" style="left:178px;top:40px;width:134px;height:118px;border-radius:50%;background:radial-gradient(circle,#f7d7cf 0%,#f4e6df 50%,#ffffff 100%);"></div>
    <div class="logo">Bloom Beauty Hub</div>
    <div class="handle">@bloombeautyhub</div>
    <h2 class="headline">Chairs Filled<br>Fast</h2>
    <p class="tagline">Attract more<br>clients with simple,<br>strategic digital marketing.</p>
    <div class="body-copy">
      <p>Chairs Filled Fast educates on the ins and outs of sponsored social media ads. With easy-to-follow video training, you’ll establish your online presence and increase salon bookings.</p>
      <p>Learn how to show up on social media with effective strategies that work. Choose our Handled Entirely system, or learn to do it all with our DIY system.</p>
    </div>
    <div class="contact-row">
      <span><svg viewBox="0 0 10 10"><path d="M2 1 L4 3 L3 4 C4 6 5 7 6 7 L7 6 L9 8 L7.5 9.5 C4 9 1 6 0.5 2.5 Z" fill="currentColor"/></svg>(+614) 0382 5519</span>
      <span><svg viewBox="0 0 10 10"><rect x="0.5" y="2" width="9" height="6" fill="none" stroke="currentColor"/><path d="M0.5 2 L5 5.5 L9.5 2" fill="none" stroke="currentColor"/></svg>hello@bloombeautyhub.com</span>
      <span><svg viewBox="0 0 10 10"><circle cx="5" cy="5" r="4.3" fill="none" stroke="currentColor"/><path d="M0.7 5 H9.3 M5 0.7 V9.3" stroke="currentColor"/></svg>www.bloombeautyhub.com</span>
    </div>
  </section>

</body>
</html>
```